Wine Label Design-Hollow Creek Vineyard

Hollow Creek Vineyard is in the Barossa Valley in South Australia. The Barossa is recognized as Australia's premier wine region, producing Australia's icon wines and some " new takes on traditional".
This family owned and operated vineyard grows some exceptionally high quality fruit. Most of the fruit is sold and used for some of Australia's most iconic wines. Small quantities are retained by the owners for some wines with very limited availability. (Wines were previously sold as Brackwell Vineyards Hollow Creek ( Shiraz, Cabernet etc).

The wines will in the future be labeled simply ‘Hollow Creek Vineyard’. The label will launch this new identity for the single family single vineyard and its high quality wines which are a true expression of the vineyard and derive from the Hollow Creek common to this ancient area (800-2000 million years old).
The label should reflect
• Single vineyard, family owned
• vines in very old rock & soils
• High quality & reliability
• Edgy but true, design based thinking (Please note:blue is generally seen as an unacceptable colour for a wine label?? Don’t ask me why)

The wines will be sold mostly direct in Australia ( ie not through retail stores), with limited export to Asia, Scandinavia and Canada.
There are three quality levels and price points in the portfolio
1. Entry level premium for everyday drinking for discriminating drinkers-approx AUD20
2. Super Premium-approx AUD30
3. Limited Release ultlra premium-AUD75-90?
We envisage three variations on the label but with an obvious & common design element. This design element should be able to be used for corporate identification and promotion
The paper stock will be waterproof and self adhesive. Our preference is for designs that engage the user by appealing to both sight and touch. It is preferred that textures be added eg embossing, high build varnish etc-rather than be a facet of the stock itself.
For information on statutory label requirements refer to www.vintnerregistry-example.com . In brief
o Front label need not show any mandatory information. However we would prefer Variety, Barossa Valley, Year and alcohol to be shown on the front label
o Back label should show all mandatories and allow for a bar code
Updates

Project Deadline Extended
Reason: I've had a problem with my wireless broadband account and reception has been intermittent to say the least to the extent that I switched off at the weekend. Just going downtown now for a 'polite discussion' with my service provider.

Project Deadline Extended
Reason: I have receiver insufficient designs of quality which we would consider. Too many designs have a "cut and paste" appearance - too few exhibit an original art/design element which truly identifies the product.

Gals & Guys

most of the designs submitted lack punch and originality and are totally unmemorable.
Please-get on Searcho or whatever enter "Wine Label Designs" and do some research b4 u waste your time and mine. Formulaic cut and paste will not win the day. That's not to say that cut and paste can't work-but it must have some originality, impact and command attention. Please surprise me.

Following on from a question from a designer about who is our competition and what we are looking for I sent the following 
"I don't think I can add anything new. Read the brief and comments again and research wine labels on the web. In 30 minutes you'll get a good idea of the creative edgy designs in the industry. There are a plethora of collections. Our competition-anyone with a label. In 2010 there were over 2400 "producers" in other words 2400 producers with at least one label. In fact there are over 25000 Australian wines and then the numerous imported wines.

Target Market(s)

$20 people who budget everyday but have graduated from drinking 'entry level' wines. These people will likely fit into Cat. (b) in the $30 wine

$30 (a) will not over-compromise on some everyday discretionary expenditure.(b) might buy for special occasions

$70-$90 Professional/successful people with high disposable/discretionary income not particularly worried about recession. wine geeks.

Industry/Entity Type

Retail

Requirements
Must have
• identifiable element across range of wines

```html
<!DOCTYPE html>
<html lang="en">
<head>
<meta charset="utf-8">
<title>Hollow Creek Vineyard – Shiraz Label</title>
<link rel="stylesheet" href="https://fonts.googleapis.com/css2?family=Fondamento&family=Jost:wght@400&display=swap">
<style>
  :root {
    --night: #050505;
    --parchment: #ebe1c3;
    --parchment-deep: #d9c9a0;
    --gold: #8c7a26;
    --ink: #111111;
    --stain: #a42a8e;
    --stain-dark: #8c1f3a;
    --rock-ochre: #d69a3a;
    --rock-pale: #e8dc8a;
    --rock-grey: #9aa89a;
  }
  html, body {
    margin: 0;
    padding: 0;
    width: 1200px;
    height: 2571px;
    overflow: hidden;
    background: var(--parchment);
  }
  .label {
    position: relative;
    width: 1200px;
    height: 2571px;
    overflow: hidden;
    background:
      radial-gradient(ellipse at 20% 85%, rgba(150,120,70,0.18), transparent 40%),
      radial-gradient(ellipse at 85% 95%, rgba(140,110,60,0.22), transparent 35%),
      linear-gradient(to bottom,
        var(--night) 0%,
        var(--night) 26%,
        #2a2620 36%,
        #8f8468 46%,
        var(--parchment-deep) 54%,
        var(--parchment) 66%,
        var(--parchment) 88%,
        var(--parchment-deep) 100%);
  }
  .brand {
    position: absolute;
    top: 40px;
    left: 0;
    width: 100%;
    text-align: center;
    color: var(--gold);
  }
  .brand-name {
    margin: 0;
    font-family: "Fondamento", serif;
    font-weight: 400;
    font-size: 210px;
    line-height: 180px;
    letter-spacing: 2px;
  }
  .brand-sub {
    margin: 50px 0 0;
    font-family: "Jost", sans-serif;
    font-size: 72px;
    letter-spacing: 16px;
    line-height: 1;
    padding-left: 16px;
  }
  .emblem {
    position: absolute;
    left: 20px;
    top: 660px;
    width: 1160px;
    height: 1160px;
  }
  .details {
    position: absolute;
    left: 0;
    width: 100%;
    text-align: center;
    font-family: "Jost", sans-serif;
    color: var(--ink);
    margin: 0;
    line-height: 1;
  }
  .variety { top: 1955px; font-size: 78px; letter-spacing: 12px; padding-left: 12px; }
  .region { top: 2138px; font-size: 56px; letter-spacing: 9px; padding-left: 9px; }
  .vintage { top: 2232px; font-size: 56px; letter-spacing: 8px; padding-left: 8px; }
  .alcohol { top: 2475px; font-size: 31px; letter-spacing: 1px; }
</style>
</head>
<body>
  <main class="label">
    <header class="brand">
      <h1 class="brand-name">Hollow<br>Creek</h1>
      <p class="brand-sub">VINEYARD</p>
    </header>

    <svg class="emblem" viewBox="0 0 1160 1160" xmlns="http://www.w3.org/2000/svg">
      <defs>
        <linearGradient id="rock-tones" x1="0" y1="0" x2="1" y2="1">
          <stop offset="0" stop-color="#e2c470"/>
          <stop offset="0.3" stop-color="#d08a36"/>
          <stop offset="0.55" stop-color="#a7b2a0"/>
          <stop offset="0.8" stop-color="#ecdf90"/>
          <stop offset="1" stop-color="#b8a27a"/>
        </linearGradient>
        <linearGradient id="stain-tone" x1="0" y1="0" x2="1" y2="0">
          <stop offset="0" stop-color="var(--stain)"/>
          <stop offset="0.8" stop-color="var(--stain)"/>
          <stop offset="1" stop-color="var(--stain-dark)"/>
        </linearGradient>
      </defs>
      <circle class="stain-ring" cx="580" cy="580" r="535" fill="none" stroke="url(#stain-tone)" stroke-width="86" opacity="0.92"/>
      <circle class="rock-photo" cx="592" cy="590" r="492" fill="url(#rock-tones)" role="img" aria-label="Close-up photograph of broken ancient vineyard rock in ochre, cream and grey tones"/>
    </svg>

    <p class="details variety">SHIRAZ</p>
    <p class="details region">BAROSSA VALLEY</p>
    <p class="details vintage">2007</p>
    <p class="details alcohol">14.0% ALC/VOL</p>
  </main>
</body>
</html>
```